Design letter head and business card

Hello,

you should design a business card and letter paper for Kranichflug Marketing. In German we write this word with K insteat of C.

Company does not have a logo. But in general, we write Kranichflug Marketing in 2 lines.
First line red: KRANICHFLUG
Second line gray: MARKETING

Red (or wine red) and Gray / Black are our favorite colors.

Company slogan: "Fresh Ground Online Marketing".

Company offers SEO, SEM, SEA, AdWords, Conversion Optimization, Online Markting Consulting ...

The website is old, please do not use this as base for your task.

German letter paper sizes:
Viawable Dimensions : 210 x 297 mm
Needed file dimensions: 212 x 299 mm

Informations to include:

Address:
Kranichflug Marketing GmbH
Lindenweg 23
71592 Weinstadt
Germany

Geschäftsführer | CEO: Bernhard Olzner

Phone: +49 (0) 7151 846 27 05

Fax: +49 (0) 7151 846 27 88

Mail: info@kranichflug-beispiel.de

Web: www.kranichflug-beispiel.de

Amtsgericht Suttgart, HRB 537264

Bank: Rosenauer Bank
IBAN: DE827315480900XXXXXXXX
BIC: GENODES1RSQ

Thanks

Bernhard

Target Market(s)

People who likes to win the online marketing game.

Industry/Entity Type

Business

Contact Information for Business Card

Here is the personal text on the card:

Name:
Bernhard Olzner

Title:
Geschäftsführer | CEO

Address:
Kranichflug Marketing GmbH
Lindenweg 23
71592 Weinstadt
Germany

Phone:
+49 (0) 7151 846 27 05

Fax:
+49 (0) 7151 846 27 88

Mail:
olzner@kranichflug-beispiel.de

Web:
www.kranichflug-beispiel.de

Business Card:
Viewable Dimensions: 85 x 55 mm
Needed file dimensions: 87 x 57mm

Font styles to use
Sans Serif

Requirements
Nice to have
• It would be great to see the dynamics of a helicopter.

```html
<!DOCTYPE html>
<html lang="de">
<head>
<meta charset="utf-8">
<title>Kranichflug Marketing – Visitenkarte Rückseite</title>
<link rel="stylesheet" href="https://fonts.googleapis.com/css2?family=Saira+Condensed:wght@600;700&family=Pathway+Gothic+One&display=swap">
<style>
  :root {
    --paper: #e6e6e7;
    --wine: #8b1f22;
    --ink: #252525;
    --mark-grey: #8a8a8a;
  }
  * { margin: 0; padding: 0; box-sizing: border-box; }
  html, body {
    width: 667px;
    height: 1200px;
    overflow: hidden;
    background: var(--paper);
  }
  .card-back {
    position: relative;
    width: 667px;
    height: 1200px;
    background: var(--paper);
  }
  .brand-dot {
    position: absolute;
    top: 340px;
    left: 273px;
    width: 120px;
    height: 120px;
    border-radius: 50%;
    background: var(--mark-grey);
  }
  .brand-name {
    position: absolute;
    top: 550px;
    left: 0;
    width: 100%;
    font-family: "Saira Condensed", sans-serif;
    font-weight: 700;
    font-size: 76px;
    line-height: 64px;
    text-align: center;
    text-transform: uppercase;
  }
  .brand-name-top {
    display: block;
    color: var(--ink);
    letter-spacing: 1px;
  }
  .brand-name-bottom {
    display: block;
    color: var(--wine);
    letter-spacing: 5px;
  }
  .slogan {
    position: absolute;
    top: 691px;
    left: 0;
    width: 100%;
    text-align: center;
    font-family: "Pathway Gothic One", sans-serif;
    font-size: 37px;
    color: var(--ink);
    letter-spacing: 0.5px;
  }
  .website {
    position: absolute;
    top: 1070px;
    left: 0;
    width: 100%;
    text-align: center;
    font-family: "Saira Condensed", sans-serif;
    font-weight: 700;
    font-size: 40px;
    color: var(--wine);
  }
  .footer-band {
    position: absolute;
    left: 0;
    bottom: 0;
    width: 100%;
    height: 52px;
    background: var(--wine);
  }
</style>
</head>
<body>
  <main class="card-back">
    <div class="brand-dot"></div>
    <h1 class="brand-name">
      <span class="brand-name-top">Kranichflug</span>
      <span class="brand-name-bottom">Marketing</span>
    </h1>
    <p class="slogan">Fresh Ground Online Marketing</p>
    <p class="website">www.kranichflug-beispiel.de</p>
    <div class="footer-band"></div>
  </main>
</body>
</html>
```